New Wix logo and website layout

I need a new logo design and a new, modern website layout design. I am a professional therapist providing remedial massage. I am Canadian but live in Australia & would like the logo to have a somewhat 'Canadian feel' to it (something subtle i.e. no flags) I currently have a maple tree leaf as my logo. my current website is tidewaterbodywork.com.au. I need the website to work on mobile phones & traditional web browsers.

Target Market(s)

customers looking for remedial massage and manual lymphatic drainage

Industry/Entity Type

professional massage

Coding

Coded - Design and coding required

Font styles to use
Sans Serif

Colors
EB3D1F
EC4F4E
F09395
F8D3D4
FCEDEE

Requirements
Nice to have
• something subtle that indicates that I am canadian
Should not have
• no flags. nothing too bold

```html
<!DOCTYPE html>
<html lang="en">
<head>
<meta charset="utf-8">
<title>Tidewater Bodywork</title>
<link href="https://fonts.googleapis.com/css2?family=Lustria&family=Roboto:wght@400;500;700&display=swap" rel="stylesheet">
<style>
:root{
  --red:#EB3D1F;
  --rose:#EC4F4E;
  --blush:#F09395;
  --pink:#F8D3D4;
  --mist:#FCEDEE;
  --ink:#222;
  --grey:#8a8a8a;
  --dark:#0f0706;
  --white:#fff;
}
*{margin:0;padding:0;box-sizing:border-box}
html,body{width:1200px;height:3665px;overflow:hidden}
body{position:relative;font-family:'Roboto',sans-serif;color:var(--ink);background:var(--white)}
.abs{position:absolute}
.serif{font-family:'Lustria',serif}
.topline{left:0;top:0;width:1200px;height:4px;background:var(--red)}
.brand{left:112px;top:55px;font-family:'Lustria',serif;font-size:19px;color:var(--ink);display:flex;align-items:center;gap:8px}
.brand-dot{width:14px;height:14px;border-radius:50%;background:var(--red)}
.contact-chip{display:flex;gap:12px;align-items:center}
.chip-icon{width:40px;height:40px;border-radius:50%;background:var(--rose);display:flex;align-items:center;justify-content:center}
.chip-label{font-size:13px;color:var(--ink)}
.chip-value{font-size:15px;font-weight:500;color:var(--ink)}
.chip-value.phone{font-size:20px;color:var(--red)}
.nav{left:463px;top:83px;display:flex;gap:26px;font-size:15px;color:#333}
.nav .active{color:var(--red)}
.hero{left:0;top:124px;width:1200px;height:631px;background:linear-gradient(100deg,#f4ecea 0%,#e9dcd8 30%,#e2a186 55%,#e35a2b 70%,#e9c7b8 88%,#ede3df 100%)}
.hero-shade{left:0;top:124px;width:620px;height:631px;background:linear-gradient(90deg,rgba(80,40,30,.35),rgba(80,40,30,0))}
.hero-eyebrow{left:108px;top:268px;font-size:36px;color:var(--white);text-shadow:0 2px 6px rgba(0,0,0,.3)}
.hero-title{left:108px;top:322px;font-size:52px;color:var(--white);text-shadow:0 2px 6px rgba(0,0,0,.3)}
.hero-text{left:108px;top:403px;width:445px;font-size:15px;line-height:26px;color:var(--white);text-align:justify}
.btn{display:flex;align-items:center;justify-content:center;gap:10px;border-radius:24px;font-weight:700;font-size:14px;color:var(--white);background:var(--rose)}
.btn-ghost{background:transparent;border:2px solid var(--white)}
.btn-arrow{width:13px;height:13px;border-radius:50%;background:var(--white);display:inline-block;position:relative}
.btn-arrow:after{content:"";position:absolute;left:5px;top:3px;border-left:5px solid var(--rose);border-top:3.5px solid transparent;border-bottom:3.5px solid transparent}
h2.section-title{font-family:'Lustria',serif;font-weight:400;font-size:35px;color:var(--ink)}
.underline{height:3px;width:44px;background:var(--red)}
.about-photo{left:128px;top:818px;width:414px;height:414px;border-radius:50%;border:3px solid var(--rose);background:radial-gradient(circle at 40% 35%,#e8c8ad,#b98a6c 55%,#7f6456)}
.about-text{left:598px;width:460px;font-size:15px;line-height:23.5px;text-align:justify;color:#333}
.about-text em{font-style:normal;color:var(--red)}
.remedial-bg{left:0;top:1295px;width:1200px;height:624px;background:linear-gradient(90deg,#fbe8e8,#f7dcdc 50%,#fae6e6)}
.remedial-text{left:120px;top:1550px;width:430px;font-size:15px;line-height:25.7px;text-align:justify;color:#333}
.card{width:203px;height:183px;background:var(--white);box-shadow:0 2px 10px rgba(0,0,0,.12);border-radius:3px;display:flex;flex-direction:column;align-items:center;justify-content:flex-end;padding-bottom:22px;text-align:center;font-weight:500;font-size:15px;line-height:24px;color:#222}
.card.featured{background:var(--rose);color:var(--white)}
.card-icon{width:62px;height:70px;border-radius:50%;border:2px solid var(--rose);margin-bottom:12px}
.card.featured .card-icon{border-color:var(--white)}
.dot{width:16px;height:16px;border-radius:50%}
.service{width:320px;text-align:center}
.service-ring{width:222px;height:222px;border-radius:50%;border:2px dotted var(--rose);margin:0 auto;position:relative}
.service-photo{position:absolute;left:11px;top:11px;width:196px;height:196px;border-radius:50%}
.service-badge{position:absolute;left:80px;top:180px;width:62px;height:62px;border-radius:50%;background:var(--rose);border:3px solid var(--white)}
.service-name{margin-top:42px;font-weight:500;font-size:18px}
.service-desc{margin-top:10px;font-size:14px;line-height:24px;color:var(--grey)}
.arrow-btn{width:30px;height:30px;border-radius:50%;background:var(--white);box-shadow:0 1px 6px rgba(0,0,0,.2)}
.fee-bg{left:0;top:2548px;width:1200px;height:627px;background:linear-gradient(180deg,#fbe4e3,#f6d2cf 60%,#f3c4bd)}
.fee-card{top:2700px;width:289px;height:348px;background:var(--white);box-shadow:0 3px 14px rgba(0,0,0,.1);text-align:center;padding-top:50px}
.fee-name{font-weight:500;font-size:17px}
.fee-price{font-weight:500;font-size:30px;color:var(--red);margin-top:8px}
.fee-list{list-style:none;text-align:left;margin:20px 0 0 38px;font-size:15px;line-height:37px;color:#333}
.fee-list li{display:flex;align-items:center;gap:12px}
.tick{width:14px;height:14px;border-radius:50%;background:var(--rose);position:relative;flex:none}
.tick:after{content:"";position:absolute;left:4px;top:2px;width:4px;height:7px;border:solid var(--white);border-width:0 2px 2px 0;transform:rotate(45deg)}
.fee-btn{width:160px;height:42px;margin:22px auto 0;font-size:14px}
.footer{left:0;top:3175px;width:1200px;height:434px;background:var(--dark)}
.foot-head{font-weight:700;font-size:15px;color:var(--white)}
.foot-rule{height:1px;width:290px;background:rgba(255,255,255,.5)}
.field{left:110px;width:290px;height:35px;background:var(--white);border-radius:18px;font-size:14px;color:#999;padding:10px 16px}
.links{list-style:none;font-size:15px;color:var(--white);line-height:34px}
.links li:before{content:"»";color:var(--red);margin-right:14px}
.social{width:33px;height:33px;border-radius:50%;border:1px solid var(--white)}
.contact-line{left:842px;display:flex;gap:14px;align-items:center;color:var(--white);font-size:15px;line-height:20px}
.contact-icon{width:32px;height:32px;border-radius:50%;background:var(--rose);flex:none}
.copyright{left:0;top:3609px;width:1200px;height:56px;background:var(--rose);color:var(--white);font-size:15px;display:flex;align-items:center;justify-content:center}
</style>
</head>
<body>

<div class="abs topline"></div>
<div class="abs brand"><span class="brand-dot"></span>Tidewater Bodywork</div>

<div class="abs contact-chip" style="left:574px;top:20px">
  <div class="chip-icon"><svg width="20" height="14" viewBox="0 0 20 14"><rect x="1" y="1" width="18" height="12" rx="1" fill="none" stroke="#fff" stroke-width="2"/><path d="M1 1l9 7 9-7" fill="none" stroke="#fff" stroke-width="2"/></svg></div>
  <div><div class="chip-label">Email Us</div><div class="chip-value">mara@tidewaterbodywork.com.au</div></div>
</div>
<div class="abs contact-chip" style="left:893px;top:20px">
  <div class="chip-icon"><svg width="18" height="18" viewBox="0 0 24 24"><path d="M6.6 10.8a15 15 0 006.6 6.6l2.2-2.2a1 1 0 011-.25 11.4 11.4 0 003.6.6 1 1 0 011 1V20a1 1 0 01-1 1A17 17 0 013 4a1 1 0 011-1h3.5a1 1 0 011 1 11.4 11.4 0 00.6 3.6 1 1 0 01-.25 1z" fill="#fff"/></svg></div>
  <div><div class="chip-label">Contact Us</div><div class="chip-value phone">0400 555 718</div></div>
</div>

<nav class="abs nav">
  <span class="active">HOME</span><span>|</span><span>REMEDIAL MASSAGE</span><span>|</span><span>ABOUT ME</span><span>|</span><span>FEES</span><span>|</span><span>CONTACT US</span>
</nav>

<div class="abs hero" role="img" aria-label="Red autumn leaf hanging over calm water with its reflection"></div>
<div class="abs hero-shade"></div>
<div class="abs hero-eyebrow serif">Welcome To</div>
<div class="abs hero-title serif">Tidewater Bodywork</div>
<p class="abs hero-text">I completed my training in Toronto, Canada in 1999 where I obtained a Diploma of Remedial Massage through the Northern College of Massage Therapy.</p>
<div class="abs btn btn-ghost" style="left:108px;top:508px;width:178px;height:45px">GET STARTED <span class="btn-arrow"></span></div>

<svg class="abs" style="left:0;top:680px" width="1200" height="80" viewBox="0 0 1200 80">
  <polygon points="0,80 0,75 285,13 590,75 883,13 1200,75 1200,80" fill="#fff"/>
  <polygon points="72,70 285,23 490,70 285,37" fill="#EB3D1F"/>
  <polygon points="676,70 883,23 1095,70 883,37" fill="#EB3D1F"/>
</svg>

<div class="abs about-photo" role="img" aria-label="Therapist giving a back massage to a client"></div>
<h2 class="abs section-title" style="left:598px;top:850px">About Me</h2>
<div class="abs underline" style="left:598px;top:895px"></div>
<p class="abs about-text" style="top:922px">I completed my training in Toronto, Canada in <em>1999</em> where I obtained a Diploma of Remedial Massage through the Northern College of Massage Therapy.</p>
<p class="abs about-text" style="top:1010px">Over the years, I have practiced in several different settings including medical centre, chiropractic clinic, spa and currently am a sole trader in my own practice. I have been helping my clients achieve better health through my treatments for several years. I take special interest in women's health.</p>
<div class="abs btn" style="left:598px;top:1150px;width:178px;height:45px">LEARN MORE <span class="btn-arrow"></span></div>

<div class="abs remedial-bg" role="img" aria-label="Soft faded photo of a massage session"></div>
<svg class="abs" style="left:0;top:1290px" width="1200" height="70" viewBox="0 0 1200 70">
  <polygon points="0,0 1200,0 1200,8 883,62 590,8 285,62 0,8" fill="#fff"/>
  <polygon points="72,12 285,50 490,12 285,40" fill="#EB3D1F"/>
  <polygon points="676,12 883,50 1075,12 883,40" fill="#EB3D1F"/>
</svg>
<h2 class="abs section-title" style="left:120px;top:1480px">Remedial Massage</h2>
<div class="abs underline" style="left:120px;top:1526px"></div>
<p class="abs remedial-text">Remedial massage is used to help relieve tension and stress in the soft tissues of the body including muscles, tendons, ligaments and connective tissue. It helps to alleviate soft tissue discomfort associated with everyday and occupational stress, over-use injuries e.g. tendinitis, and many chronic pain conditions. &nbsp;An increase in circulation and increased joint flexibility are additional benefits.</p>
<div class="abs btn" style="left:120px;top:1752px;width:178px;height:45px">LEARN MORE <span class="btn-arrow"></span></div>

<div class="abs card" style="left:648px;top:1453px"><div class="card-icon" role="img" aria-label="Line icon of a person with an arm sling"></div>Aids in recovery of<br>sporting injuries</div>
<div class="abs card featured" style="left:871px;top:1421px"><div class="card-icon" role="img" aria-label="Line icon of a person holding their head"></div>Reduces/prevents<br>headaches</div>
<div class="abs card" style="left:648px;top:1659px"><div class="card-icon" role="img" aria-label="Line icon of a person resting on a massage table"></div>Reduces levels of<br>anxiety</div>
<div class="abs card" style="left:871px;top:1627px"><div class="card-icon" role="img" aria-label="Line icon of a pregnant woman"></div>Assists with pregnancy<br>discomfort</div>
<div class="abs dot" style="left:952px;top:1834px;background:var(--rose)"></div>
<div class="abs dot" style="left:978px;top:1834px;background:var(--white);border:1px solid var(--blush)"></div>

<h2 class="abs section-title" style="left:0;width:1200px;text-align:center;top:2005px">Our Services</h2>
<div class="abs underline" style="left:578px;top:2050px"></div>
<div class="abs arrow-btn" style="left:55px;top:2275px"></div>
<div class="abs arrow-btn" style="left:1115px;top:2275px"></div>

<div class="abs service" style="left:98px;top:2092px">
  <div class="service-ring"><div class="service-photo" style="background:radial-gradient(circle,#e9c3a8,#c99478)" role="img" aria-label="Hands massaging a client's shoulder"></div><div class="service-badge"></div></div>
  <div class="service-name">Remedial</div>
  <p class="service-desc">Lorem ipsum dolor sited ameted consectetur adipiscing &nbsp;eiusmod tempor incididunt labore dolore magna aliqua &nbsp;enim &nbsp;minim veniam.</p>
</div>
<div class="abs service" style="left:442px;top:2092px">
  <div class="service-ring"><div class="service-photo" style="background:radial-gradient(circle,#e7cfbd,#a27a63)" role="img" aria-label="Couple relaxing during a spa massage"></div><div class="service-badge"></div></div>
  <div class="service-name">Therapeutic</div>
  <p class="service-desc">Lorem ipsum dolor sited ameted consectetur adipiscing &nbsp;eiusmod tempor incididunt labore dolore magna aliqua &nbsp;enim &nbsp;minim veniam.</p>
</div>
<div class="abs service" style="left:786px;top:2092px">
  <div class="service-ring"><div class="service-photo" style="background:radial-gradient(circle,#f3ece6,#c9b4a4)" role="img" aria-label="Pregnant woman resting at home"></div><div class="service-badge"></div></div>
  <div class="service-name">Pregnancy</div>
  <p class="service-desc">Lorem ipsum dolor sited ameted consectetur adipiscing &nbsp;eiusmod tempor incididunt labore dolore magna aliqua &nbsp;enim &nbsp;minim veniam.</p>
</div>

<div class="abs fee-bg" role="img" aria-label="Faded city skyline with autumn trees"></div>
<h2 class="abs section-title" style="left:0;width:1200px;text-align:center;top:2612px">Fee Schedule</h2>
<div class="abs underline" style="left:578px;top:2656px"></div>

<div class="abs fee-card" style="left:129px">
  <div class="fee-name">30 min Remedial Massage</div><div class="fee-price">$70</div>
  <ul class="fee-list"><li><span class="tick"></span>Lorem ipsum dolor sit amet</li><li><span class="tick"></span>Lorem ipsum dolor sit amet</li><li><span class="tick"></span>Lorem ipsum dolor sit amet</li></ul>
  <div class="btn fee-btn">GET STARTED</div>
</div>
<div class="abs fee-card" style="left:455px">
  <div class="fee-name">45 &nbsp;min Remedial Massage</div><div class="fee-price">$90</div>
  <ul class="fee-list"><li><span class="tick"></span>Lorem ipsum dolor sit amet</li><li><span class="tick"></span>Lorem ipsum dolor sit amet</li><li><span class="tick"></span>Lorem ipsum dolor sit amet</li></ul>
  <div class="btn fee-btn">GET STARTED</div>
</div>
<div class="abs fee-card" style="left:781px">
  <div class="fee-name">90 min Remedial Massage</div><div class="fee-price">$160</div>
  <ul class="fee-list"><li><span class="tick"></span>Lorem ipsum dolor sit amet</li><li><span class="tick"></span>Lorem ipsum dolor sit amet</li><li><span class="tick"></span>Lorem ipsum dolor sit amet</li></ul>
  <div class="btn fee-btn">GET STARTED</div>
</div>
<div class="abs dot" style="left:575px;top:3090px;width:13px;height:13px;background:var(--red)"></div>
<div class="abs dot" style="left:593px;top:3090px;width:13px;height:13px;background:var(--blush)"></div>
<div class="abs dot" style="left:611px;top:3090px;width:13px;height:13px;background:var(--red)"></div>

<div class="abs footer"></div>
<svg class="abs" style="left:0;top:3105px" width="1200" height="75" viewBox="0 0 1200 75">
  <polygon points="0,75 0,70 307,8 600,70 906,8 1200,70 1200,75" fill="#0f0706"/>
  <polygon points="104,68 307,12 520,68 307,28" fill="#EB3D1F"/>
  <polygon points="706,68 906,12 1125,68 906,28" fill="#EB3D1F"/>
</svg>

<div class="abs foot-head" style="left:110px;top:3240px">GET IN TOUCH</div>
<div class="abs foot-rule" style="left:110px;top:3275px"></div>
<div class="abs field" style="top:3302px">Ente Name*</div>
<div class="abs field" style="top:3353px">Enter Email*</div>
<div class="abs field" style="top:3405px;height:80px;border-radius:14px">Message*</div>
<div class="abs btn" style="left:110px;top:3503px;width:288px;height:47px">SUBSCRIBE NOW <span class="btn-arrow"></span></div>

<div class="abs foot-head" style="left:566px;top:3240px">USEFUL LINKS</div>
<ul class="abs links" style="left:566px;top:3286px"><li>Home</li><li>Remedial Massage</li><li>About Me</li><li>Fees</li><li>Contact Us</li></ul>
<div class="abs social" style="left:561px;top:3479px"></div>
<div class="abs social" style="left:603px;top:3479px"></div>
<div class="abs social" style="left:645px;top:3479px"></div>
<div class="abs social" style="left:687px;top:3479px"></div>

<div class="abs foot-head" style="left:842px;top:3240px">CONTACT &nbsp;US</div>
<div class="abs contact-line" style="top:3299px"><span class="contact-icon"></span>0400 555 718</div>
<div class="abs contact-line" style="top:3349px"><span class="contact-icon"></span>mara@tidewaterbodywork.com.au</div>
<div class="abs contact-line" style="top:3400px"><span class="contact-icon"></span>Mara Linden 24 Harbour Lane<br>Seaview VIC 3199</div>
<div class="abs" style="left:847px;top:3469px;width:215px;height:50px;background:var(--white)" role="img" aria-label="Professional association membership badge"></div>

<div class="abs copyright">2022 Copyright - &nbsp;Tidewater Bodywork &nbsp;| &nbsp;All Rights Reserved</div>

</body>
</html>
```